Letter design, envelope design, and more

Hello, we the Tavrin Gmbh are looking for our shop. Letter C5. Design does not have to be like a business card, so it can have straight lines. Only the color is important. The logo is the text under TaVRin omit.It should not be playful but Profesionel

Font styles to use
Sans Serif

Colors
0555a3
3176b5
85abd2
85cae6
34a7d8
0792cd
cee9f5
cfdfed
000000

Requirements
Must have
• Color like business card, Please, with the text under TaVRin, Correct address Lindmattstr. 4 Zip code 9517 Tellbach, as well as Couvert Without addressing only design and logo with TaVrn
Nice to have
• more writing articles
Should not have
• Not too colored, Text under TaVRin, bright colors

```html
<!DOCTYPE html>
<html lang="en">
<head>
<meta charset="utf-8">
<title>Tavrin Gmbh – Stationery</title>
<link href="https://fonts.googleapis.com/css2?family=Lato:wght@400;700&family=Kaushan+Script&display=swap" rel="stylesheet">
<style>
:root{
  --stage:#555759;
  --navy:#26296b;
  --steel:#7e9db8;
  --paper:#ffffff;
  --ink:#3a3a44;
  --hairline:#c9c9cf;
}
*{margin:0;padding:0;box-sizing:border-box}
html,body{width:1200px;height:698px;overflow:hidden;background:var(--stage)}
body{position:relative;font-family:"Lato",sans-serif;color:var(--ink)}
.sheet{position:absolute;background:var(--paper)}
.brand{position:absolute;display:flex;align-items:center;gap:6px;font-family:"Lato",sans-serif;font-weight:700;color:var(--navy);letter-spacing:.06em;white-space:nowrap}
.brand-mark{display:block;background:var(--steel)}
.brand--light{color:var(--paper)}
.web{font-size:9px;letter-spacing:.22em;color:var(--ink);white-space:nowrap}
.web b{font-weight:400;color:var(--steel)}

/* letterhead */
.letter{left:28px;top:78px;width:386px;height:542px}
.letter .brand{left:22px;top:14px;font-size:22px}
.letter .brand-mark{width:30px;height:30px}
.letter-rule{position:absolute;top:62px;height:1px;background:var(--navy)}
.letter .web{position:absolute;left:277px;top:56px}
.salutation{position:absolute;left:22px;top:92px;font-size:9.6px;font-weight:700;color:var(--navy)}
.body-copy{position:absolute;left:22px;top:113px;width:346px}
.body-copy p{font-size:7.1px;line-height:11.6px;text-align:justify;margin-bottom:10.5px;color:#4a4a52}
.closing{position:absolute;left:22px;top:420px;font-size:11.5px;color:#44444c}
.signature{position:absolute;left:22px;top:436px;font-family:"Kaushan Script",cursive;font-size:20px;color:var(--navy)}
.letter-footer{position:absolute;left:0;right:0;top:524px;display:flex;justify-content:center;gap:7px;font-size:7.4px;color:#44444c;align-items:center}
.letter-footer span{display:flex;align-items:center;gap:3px}
.sep{width:1px;height:9px;background:var(--hairline)}
.icon{width:8px;height:8px;fill:none;stroke:var(--ink);stroke-width:1.3}

/* envelopes */
.envelope-back{left:596px;top:33px;width:573px;height:256px}
.envelope-back svg{position:absolute;left:0;top:0}
.envelope-back .brand{left:50%;top:38px;transform:translateX(-50%);font-size:24px}
.envelope-back .brand-mark{width:26px;height:26px;background:var(--paper)}
.envelope-mid{left:554px;top:142px;width:573px;height:256px;border:1px solid var(--hairline)}
.envelope-mid svg{position:absolute;left:0;top:0}
.envelope-mid .brand{left:50%;top:36px;transform:translateX(-50%);font-size:24px}
.envelope-mid .brand-mark{width:26px;height:26px}
.envelope-front{left:459px;top:257px;width:573px;height:256px;border:1px solid var(--hairline)}
.envelope-front .brand{left:16px;top:14px;font-size:28px}
.envelope-front .brand-mark{width:36px;height:36px}
.envelope-address{position:absolute;left:16px;top:65px;font-size:11.2px;letter-spacing:.04em;color:#333;display:flex;align-items:center;gap:5px}
.envelope-address .icon{width:10px;height:10px}
.envelope-rule{position:absolute;top:239px;height:1px;background:var(--navy)}
.envelope-front .web{position:absolute;left:240px;top:233px;font-size:10px}

/* business cards */
.card-front{left:538px;top:540px;width:212px;height:121px}
.card-front .brand{left:11px;top:12px;font-size:15px;gap:4px}
.card-front .brand-mark{width:18px;height:18px}
.card-rule{position:absolute;top:56px;height:1px;background:var(--navy)}
.card-name{position:absolute;right:13px;top:51px;font-size:7.2px;font-weight:700;color:var(--navy)}
.card-title{position:absolute;right:13px;top:61px;font-size:5.6px;color:var(--steel);letter-spacing:.04em}
.card-contacts{position:absolute;right:14px;top:89px;text-align:right;font-size:5.4px;line-height:9px;color:#333}
.card-contacts i{display:inline-block;width:5px;height:5px;border-radius:50%;border:1px solid var(--navy);margin-left:4px;vertical-align:-1px}
.card-contacts b{font-weight:400;color:var(--steel)}
.card-address{position:absolute;left:11px;top:99px;font-size:5.4px;line-height:7px;color:#333;display:flex;gap:3px;align-items:flex-start}
.card-address .icon{width:6px;height:6px;margin-top:.5px}
.card-back{left:759px;top:540px;width:211px;height:121px;background:var(--navy)}
.card-back .brand{left:50%;top:43px;transform:translateX(-50%);font-size:17px}
.card-back .brand-mark{width:20px;height:20px}
.card-back-rule{position:absolute;top:100px;height:1px;background:var(--steel)}
.card-back .web{position:absolute;left:72px;top:95px;font-size:7.4px;color:var(--paper)}
.card-back .web b{color:var(--paper)}
</style>
</head>
<body>

<section class="sheet letter" aria-label="Letterhead">
  <div class="brand"><span class="brand-mark"></span>TAVRIN</div>
  <div class="letter-rule" style="left:0;width:268px"></div>
  <div class="web">www.<b>tavrin</b>.ch</div>
  <div class="letter-rule" style="left:369px;width:17px"></div>
  <p class="salutation">Dear Mr. Lorem,</p>
  <div class="body-copy">
    <p>Lorem ipsum dolor sit amet, consectetuer adipiscing elit, sed diam nonummy nibh euismod tincidunt ut laoreet dolore magna aliquam erat volutpat. Ut wisi enim ad minim veniam, quis nostrud exerci tation ullamcorper suscipit lobortis nisl ut aliquip ex ea commodo consequat. Duis autem vel eum iriure dolor in hendiusto odio dignissim qui blandit praesent luptatum zzril delenit facilisi.</p>
    <p>Lorem ipsum dolor sit amet, consectetuer adipiscing elit, sed diam nonummy nibh euismod tincidunt ut laoreet dolore magna aliquam erat volutpat. Ut wisi enim ad minim veniam, quis nostrud exerci tation ullamcorper suscipit lobortis nisl ut aliquip ex ea commodo consequat.</p>
    <p>Lorem ipsum dolor sit amet, consectetuer adipiscing elit, sed diam nonummy nibh euismod tincidunt ut laoreet dolore magna aliquam erat volutpat. Ut wisi enim ad minim veniam, quis nostrud exerci tation ullamcorper suscipit lobortis nisl ut aliquip ex ea commodo consequat. Duis autem vel eum iriure dolor in hendiusto odio dignissim qui blandit praesent luptatum zzril delenit facilisi.</p>
    <p>Lorem ipsum dolor sit amet, consectetuer adipiscing elit, sed diam nonummy nibh euismod tincidunt ut laoreet dolore magna aliquam erat volutpat. Ut wisi enim ad minim veniam, quis nostrud exerci tation ullamcorper suscipit lobortis nisl ut aliquip ex ea commodo consequat.</p>
    <p>Lorem ipsum dolor sit amet, consectetuer adipiscing elit, sed diam nonummy nibh euismod tincidunt ut laoreet dolore magna aliquam erat volutpat. Ut wisi enim ad minim veniam, quis nostrud exerci tation ullamcorper suscipit lobortis nisl ut aliquip ex ea commodo consequat. Duis autem vel eum iriure dolor in hendiusto odio dignissim qui blandit praesent luptatum zzril delenit facilisi.</p>
    <p>Lorem ipsum dolor sit amet, consectetuer adipiscing elit, sed diam nonummy nibh euismod tincidunt ut laoreet dolore magna aliquam erat volutpat. Ut wisi enim ad minim veniam, quis nostrud exerci tation ullamcorper suscipit lobortis nisl ut aliquip ex ea commodo consequat.</p>
  </div>
  <p class="closing">Sincerely Your,</p>
  <p class="signature">Your Name</p>
  <div class="letter-footer">
    <span><svg class="icon" viewBox="0 0 10 10"><circle cx="5" cy="5" r="4"/><circle cx="5" cy="4.5" r="1.3"/></svg>Lindmattstr. 4, 9517 Tellbach</span>
    <i class="sep"></i>
    <span><svg class="icon" viewBox="0 0 10 10"><circle cx="5" cy="5" r="4"/><path d="M3.5 3.2c0 2 1.3 3.5 3.2 3.6"/></svg>+41 71 555 02 40</span>
    <i class="sep"></i>
    <span><svg class="icon" viewBox="0 0 10 10"><rect x="1" y="2.5" width="8" height="5"/><path d="M1 2.5l4 3 4-3"/></svg>info@tavrin.ch</span>
  </div>
</section>

<section class="sheet envelope-back" aria-label="C5 envelope, back with open flap">
  <svg width="573" height="256" viewBox="0 0 573 256">
    <path d="M0 0H573L562 30C556 46 548 52 520 58L325 98C300 103 275 103 250 98L54 58C26 52 18 46 11 30Z" fill="var(--steel)"/>
  </svg>
  <div class="brand brand--light"><span class="brand-mark"></span>TAVRIN</div>
</section>

<section class="sheet envelope-mid" aria-label="C5 envelope, back with closed flap">
  <svg width="573" height="256" viewBox="0 0 573 256">
    <path d="M0 0L8 30C14 48 22 54 48 60L255 98C275 102 298 102 318 98L525 60C551 54 559 48 565 30L573 0" fill="none" stroke="var(--hairline)" stroke-width="1"/>
  </svg>
  <div class="brand"><span class="brand-mark"></span>TAVRIN</div>
</section>

<section class="sheet envelope-front" aria-label="C5 envelope, front">
  <div class="brand"><span class="brand-mark"></span>TAVRIN</div>
  <p class="envelope-address"><svg class="icon" viewBox="0 0 10 10"><circle cx="5" cy="5" r="4"/><circle cx="5" cy="4.5" r="1.3"/></svg>Lindmattstr. 4, 9517 Tellbach</p>
  <div class="envelope-rule" style="left:0;width:231px"></div>
  <div class="web">www.<b>tavrin</b>.ch</div>
  <div class="envelope-rule" style="left:341px;width:232px"></div>
</section>

<section class="sheet card-front" aria-label="Business card, front">
  <div class="brand"><span class="brand-mark"></span>TAVRIN</div>
  <div class="card-rule" style="left:0;width:148px"></div>
  <p class="card-name">YOUR NAME</p>
  <div class="card-rule" style="left:201px;width:11px"></div>
  <p class="card-title">TITLE</p>
  <div class="card-contacts">
    +41 71 555 02 40<i></i><br>
    info@tavrin.ch<i></i><br>
    www.<b>tavrin</b>.ch<i></i>
  </div>
  <div class="card-address"><svg class="icon" viewBox="0 0 10 10"><circle cx="5" cy="5" r="4"/><circle cx="5" cy="4.5" r="1.3"/></svg><p>Lindmattstr. 4<br>9517 Tellbach</p></div>
</section>

<section class="sheet card-back" aria-label="Business card, back">
  <div class="brand brand--light"><span class="brand-mark"></span>TAVRIN</div>
  <div class="card-back-rule" style="left:0;width:66px"></div>
  <div class="web">www.<b>tavrin</b>.ch</div>
  <div class="card-back-rule" style="left:145px;width:66px"></div>
</section>

</body>
</html>
```